Looking for someone to design a business card for my plumbing business Quandor Plumbing Solutions I want the background also to be black, must attract clients. If possible I want the front to be the logo and the back to show maybe the details.

Target Market(s)

Clients

Industry/Entity Type

Plumbing maintenance

Contact Information for Business Card

Name: Felix, Contact: 0461 539 207, Email: quandorplumbingsolutions@mailbrook.example, Licence number 728093K

Font styles to use
Other font styles liked:
• as per logo maybe?

Colors

Designer to choose colors to be used in the design.

Requirements
Nice to have
• stating the service I provide, emergency plumbing, plumbing maintenance, drainage maintenance, block sewer and stormwater, camera and locating.

```html
<!DOCTYPE html>
<html lang="en">
<head>
<meta charset="utf-8">
<title>Quandor Plumbing Solutions — Business Card</title>
<link rel="stylesheet" href="https://fonts.googleapis.com/css2?family=Raleway:wght@400;500;700&display=swap">
<style>
  :root {
    --backdrop: #d9d9d7;
    --card: #202020;
    --card-edge: #4a90d9;
    --accent: #4a90d9;
    --text: #f2f2f2;
    --emboss: #2c2c2c;
  }
  * { box-sizing: border-box; margin: 0; padding: 0; }
  html, body {
    width: 1200px; height: 801px; overflow: hidden;
    background: var(--backdrop);
    font-family: "Raleway", sans-serif;
  }
  .stage {
    width: 1200px; height: 801px;
    display: flex; align-items: center; justify-content: center; gap: 40px;
  }
  .card {
    position: relative;
    width: 540px; height: 309px;
    background: var(--card);
    border-bottom: 4px solid var(--card-edge);
    border-right: 3px solid var(--card-edge);
    box-shadow: 0 14px 28px rgba(0,0,0,0.25);
    color: var(--text);
  }
  /* details side */
  .card-details .brand {
    position: absolute; top: 34px; right: 38px; width: 240px;
    text-align: center;
    font-weight: 700; font-size: 26px; line-height: 1.1;
    color: var(--accent); text-transform: uppercase; letter-spacing: 1px;
  }
  .card-details .identity {
    position: absolute; left: 30px; top: 96px;
  }
  .identity .name {
    font-weight: 700; font-size: 22px; color: var(--accent);
    text-transform: uppercase; letter-spacing: 0.5px; line-height: 1;
  }
  .identity .role { font-size: 13px; margin-top: 3px; }
  .divider {
    position: absolute; left: 30px; right: 30px; top: 150px;
    height: 1px; background: var(--accent);
  }
  .contacts {
    position: absolute; left: 30px; top: 166px;
    list-style: none; font-size: 11.5px; line-height: 1.75;
  }
  .contacts li { display: flex; align-items: center; gap: 7px; }
  .contacts .licence { padding-left: 0; }
  .contacts svg { width: 11px; height: 11px; flex: none; }
  .services {
    position: absolute; right: 30px; top: 166px;
    list-style: none; text-align: right; font-size: 12px; line-height: 1.6;
  }
  .services li::after {
    content: ""; display: inline-block; width: 5px; height: 5px;
    border-radius: 50%; background: var(--accent);
    margin-left: 7px; vertical-align: middle;
  }
  /* logo side */
  .card-logo { display: flex; align-items: center; justify-content: center; gap: 14px; }
  .card-logo .brand-mark {
    width: 40px; height: 40px; border-radius: 50%; background: var(--emboss);
  }
  .card-logo .brand {
    font-weight: 700; font-size: 30px; line-height: 1.1;
    color: var(--emboss); text-transform: uppercase; letter-spacing: 1px;
  }
</style>
</head>
<body>
<main class="stage">
  <section class="card card-details" aria-label="Business card, details side">
    <div class="brand">Quandor Plumbing Solutions</div>
    <div class="identity">
      <p class="name">Felix</p>
      <p class="role">Founder &amp; CEO</p>
    </div>
    <div class="divider"></div>
    <ul class="contacts">
      <li class="licence">Licence number 728093K</li>
      <li>
        <svg viewBox="0 0 12 12" aria-hidden="true"><path d="M3 1 L5 3.5 L4 5 Q5 7 7 8 L8.5 7 L11 9 L9.5 11 Q4 10.5 1 3 Z" fill="#4a90d9"/></svg>
        0461 539 207
      </li>
      <li>
        <svg viewBox="0 0 12 12" aria-hidden="true"><rect x="1" y="2.5" width="10" height="7" fill="#4a90d9"/><path d="M1 2.5 L6 6.5 L11 2.5" fill="none" stroke="#202020" stroke-width="1"/></svg>
        quandorplumbingsolutions@mailbrook.example
      </li>
      <li>
        <svg viewBox="0 0 12 12" aria-hidden="true"><circle cx="6" cy="6" r="5.5" fill="#4a90d9"/></svg>
        @QuandorPlumbingSolutions
      </li>
    </ul>
    <ul class="services">
      <li>Emergency plumbing</li>
      <li>Plumbing maintenance</li>
      <li>Drainage maintenance</li>
      <li>Block sewer and stormwater</li>
      <li>Camera and locating</li>
    </ul>
  </section>

  <section class="card card-logo" aria-label="Business card, logo side">
    <span class="brand-mark"></span>
    <div class="brand">Quandor<br>Plumbing Solutions</div>
  </section>
</main>
</body>
</html>
```